New Business card design to reflect rebrand

I would like a business card design with a good base colour for our new logo and also a placeholder for a profile pic of the card holder. the design needs to be editable to the point that we can easily change the picture of the person and use that design for printmerlo etc. we are looking at a metalic finish business card so will need a good base colour to bring out the finish.

Target Market(s)

prospective customers

Industry/Entity Type

Business

Contact Information for Business Card

I would like one editable design that we can change the name of the card holder and profile picture. The design need to be in a format that be send to printmerlo etc.

Our address is Fenwick Lodge, Copse Lane, Hartley Wintney, GU14 3TP Tel no. 01483 556172

Requirements
Must have
• place holder for a profile pic for the card holder. in AI or preferably PSD format

```html
<!DOCTYPE html>
<html lang="en">
<head>
<meta charset="utf-8">
<title>Corvane Workplace Services – Business Card</title>
<link rel="stylesheet" href="https://fonts.googleapis.com/css2?family=Lato:wght@400;700;900&display=swap">
<style>
  :root {
    --orange: #eb5e0b;
    --slate: #405673;
    --white: #ffffff;
    --ink: #2f3a4a;
    --page: #eceef1;
  }
  * { margin: 0; padding: 0; box-sizing: border-box; }
  html, body { width: 1200px; height: 1200px; overflow: hidden; }
  body {
    background: var(--page);
    font-family: "Lato", sans-serif;
    display: flex;
    flex-direction: column;
    align-items: center;
    justify-content: center;
    gap: 60px;
  }
  .card {
    position: relative;
    width: 900px;
    height: 514px;
    background: var(--white);
    overflow: hidden;
    box-shadow: 0 6px 24px rgba(0,0,0,0.12);
  }
  .card-shapes { position: absolute; inset: 0; width: 100%; height: 100%; }
  .card-text { position: absolute; }

  /* Front side */
  .front .brand-name {
    left: 0; width: 700px; top: 200px;
    text-align: center;
    color: var(--slate);
    font-weight: 900;
    line-height: 1;
  }
  .front .brand-name .word { display: block; font-size: 104px; letter-spacing: 4px; }
  .front .brand-name .sub { display: block; font-size: 30px; letter-spacing: 9px; margin-top: 12px; }
  .front .web-line {
    left: 0; right: 0; top: 439px;
    text-align: center;
    color: var(--white);
    font-size: 22px;
    letter-spacing: 6px;
  }

  /* Back side */
  .back .brand-name {
    left: 0; width: 560px; top: 78px;
    text-align: center;
    color: var(--slate);
    font-weight: 900;
    line-height: 1;
  }
  .back .brand-name .word { display: block; font-size: 74px; letter-spacing: 3px; }
  .back .brand-name .sub { display: block; font-size: 22px; letter-spacing: 7px; margin-top: 10px; }
  .address-line {
    left: 84px; top: 298px;
    color: var(--white);
    font-size: 16px;
  }
  .icon { position: absolute; width: 28px; height: 28px; }
  .contact {
    color: var(--white);
    font-size: 19px;
  }
  .photo-slot {
    position: absolute;
    left: 654px; top: 124px;
    width: 218px; height: 222px;
    border: 4px solid var(--slate);
    border-radius: 12px;
    background: linear-gradient(180deg, #f4f4f4 0%, #e4e2df 55%, #2a2c31 100%);
  }
  .holder-name {
    right: 30px; top: 376px;
    color: var(--white);
    font-size: 27px;
    font-weight: 700;
  }
  .holder-role {
    right: 30px; top: 428px;
    color: var(--ink);
    font-size: 18px;
  }
</style>
</head>
<body>

  <section class="card front">
    <svg class="card-shapes" viewBox="0 0 560 320" preserveAspectRatio="none" aria-hidden="true">
      <path d="M478,0 H560 V320 H0 V235 H390 Q404,235 409,222 Z" fill="var(--orange)"/>
      <rect x="0" y="263" width="560" height="36" fill="var(--slate)"/>
    </svg>
    <div class="card-text brand-name">
      <span class="word">CORVANE</span>
      <span class="sub">WORKPLACE SERVICES</span>
    </div>
    <div class="card-text web-line">www.website.com</div>
  </section>

  <section class="card back">
    <svg class="card-shapes" viewBox="0 0 560 320" preserveAspectRatio="none" aria-hidden="true">
      <path d="M425,0 Q406,0 399,18 L340,172 H0 V320 H560 V0 Z" fill="var(--orange)"/>
      <path d="M0,172 H341 L328,204 Q325,212 316,212 H0 Z" fill="var(--slate)"/>
    </svg>

    <div class="card-text brand-name">
      <span class="word">CORVANE</span>
      <span class="sub">WORKPLACE SERVICES</span>
    </div>

    <svg class="icon" style="left:46px; top:295px;" viewBox="0 0 28 28" aria-hidden="true">
      <rect width="28" height="28" rx="5" fill="var(--orange)"/>
      <path d="M14,6 a6,6 0 0 1 6,6 c0,4 -6,10 -6,10 s-6,-6 -6,-10 a6,6 0 0 1 6,-6z" fill="var(--white)"/>
      <circle cx="14" cy="12" r="2.2" fill="var(--orange)"/>
    </svg>
    <div class="card-text address-line">Address: Street No, Nord Avenue, Co,City/State Zipcode</div>

    <svg class="icon" style="left:45px; top:389px;" viewBox="0 0 28 28" aria-hidden="true">
      <rect width="28" height="28" rx="5" fill="var(--slate)"/>
      <rect x="10" y="6" width="8" height="16" rx="1.5" fill="none" stroke="var(--white)" stroke-width="1.6"/>
    </svg>
    <div class="card-text contact" style="left:96px; top:391px;">+ 000 - 000 - 000</div>

    <svg class="icon" style="left:45px; top:438px;" viewBox="0 0 28 28" aria-hidden="true">
      <rect width="28" height="28" rx="5" fill="var(--slate)"/>
      <path d="M10,7 l3,4 -2,2 c1,2 2,3 4,4 l2,-2 4,3 -2,3 c-6,0 -11,-5 -11,-11z" fill="var(--white)"/>
    </svg>
    <div class="card-text contact" style="left:96px; top:440px;">+ 000 - 000 - 000</div>

    <svg class="icon" style="left:281px; top:389px;" viewBox="0 0 28 28" aria-hidden="true">
      <rect width="28" height="28" rx="5" fill="var(--slate)"/>
      <rect x="7" y="9" width="14" height="10" rx="1" fill="none" stroke="var(--white)" stroke-width="1.6"/>
      <path d="M7,9 l7,6 7,-6" fill="none" stroke="var(--white)" stroke-width="1.6"/>
    </svg>
    <div class="card-text contact" style="left:320px; top:391px;">mail@website.com</div>

    <svg class="icon" style="left:281px; top:438px;" viewBox="0 0 28 28" aria-hidden="true">
      <rect width="28" height="28" rx="5" fill="var(--slate)"/>
      <g fill="none" stroke="var(--white)" stroke-width="1.4">
        <circle cx="14" cy="14" r="7"/>
        <ellipse cx="14" cy="14" rx="3" ry="7"/>
        <path d="M7,14 H21 M8.5,10.5 H19.5 M8.5,17.5 H19.5"/>
      </g>
    </svg>
    <div class="card-text contact" style="left:320px; top:440px;">www.website.com</div>

    <div class="photo-slot" role="img" aria-label="Profile photo of the card holder"></div>

    <div class="card-text holder-name">CARD HOLDER NAME</div>
    <div class="card-text holder-role">JOB TITLE/POSITION</div>
  </section>

</body>
</html>
```